Ecard for facebook and Instagram postings

I need 4 ecards (don't know if that is what it is called) for Facebook and Instagram postings. My Logo and company name should be incorporated and also be square. I would like to be able to insert text as I need. Examples are:

https://www.plorvexa.com/photo.php?fbid=20262841672382489&set=a.20261729249182489.516031.71298967488&type=1&relevant_count=1

https://media-a-kpt.yy.plorvexacdn.net/hpics-bmk4/2345967_657092986477056_308792573_n.jpg

I don't necessarily need images on them, just the color scheme to my business cards and the logo and business name. But if you'd like to give it an interesting look, you can go ahead and play with it. My site is tornquillmentoring.com, if you'd like to see the style of it.

Thank you!!!
Updates

I just uploaded the logo in two variations.  Thank you!

Target Market(s)

Women 16-65

Industry/Entity Type

Business

Requirements
Must have
• Logo and business name
Should not have
• No white background. I have attached business card picture so you can have an idea of what I'd like.

```html
<!DOCTYPE html>
<html lang="en">
<head>
<meta charset="UTF-8">
<title>Tornquill Mentoring Services – Quote Card</title>
<link rel="stylesheet" href="https://fonts.googleapis.com/css2?family=Tinos:wght@700&family=Montserrat:wght@500;600&display=swap">
<style>
  :root {
    --bar-orange: #f39a1e;
    --paper-light: #f7f7f7;
    --paper-shade: #e4e4e4;
    --quote-red: #c4202e;
    --ink: #0c0c0c;
    --wine: #8e1230;
    --wine-deep: #5c0a1c;
    --rose: #e9a3b1;
    --rose-pale: #f6d6dc;
    --badge-orange: #f08a1c;
    --white: #ffffff;
  }
  * { margin: 0; padding: 0; box-sizing: border-box; }
  html, body { width: 1200px; height: 1200px; overflow: hidden; }
  body { background: var(--paper-light); }

  .card {
    position: relative;
    width: 1200px;
    height: 1200px;
    overflow: hidden;
    background: radial-gradient(ellipse at 50% 40%, var(--paper-light) 0%, #efefef 60%, var(--paper-shade) 100%);
  }
  .top-bar {
    position: absolute; top: 0; left: 0;
    width: 100%; height: 22px;
    background: var(--bar-orange);
  }
  .quote-mark {
    position: absolute;
    font-family: "Tinos", "Times New Roman", serif;
    font-weight: 700;
    font-size: 330px;
    line-height: 1;
    color: var(--quote-red);
  }
  .quote-mark--open { left: 58px; top: 60px; }
  .quote-mark--close { left: 950px; top: 810px; }

  .quote-text {
    position: absolute;
    top: 220px; left: 0;
    width: 100%;
    text-align: center;
    font-family: "Tinos", "Times New Roman", serif;
    font-weight: 700;
    font-size: 100px;
    line-height: 128px;
    color: var(--ink);
  }

  .wave-band {
    position: absolute; left: 0; bottom: 0;
    width: 1200px; height: 300px;
  }

  .brand {
    position: absolute; left: 30px; top: 995px;
    color: var(--white);
  }
  .brand-name {
    font-family: "Montserrat", Arial, sans-serif;
    font-weight: 600;
    font-size: 96px;
    line-height: 1;
    letter-spacing: 1px;
  }
  .brand-line {
    display: flex; align-items: baseline; gap: 40px;
    margin-top: 26px;
  }
  .brand-services {
    font-family: "Montserrat", Arial, sans-serif;
    font-weight: 600;
    font-size: 29px;
    letter-spacing: 8px;
  }
  .brand-url {
    font-family: "Montserrat", Arial, sans-serif;
    font-weight: 500;
    font-size: 29px;
    letter-spacing: 1px;
  }
  .brand-badge {
    position: absolute; left: 1008px; top: 1000px;
    width: 158px; height: 158px;
    border-radius: 50%;
    background: var(--badge-orange);
    border: 8px solid var(--white);
    box-shadow: 0 0 0 3px var(--rose);
  }
</style>
</head>
<body>
  <main class="card">
    <div class="top-bar"></div>

    <span class="quote-mark quote-mark--open" aria-hidden="true">&ldquo;</span>

    <p class="quote-text">Ignorance is the<br>curse of God;<br>knowledge is the<br>wing wherewith we<br>fly to heaven</p>

    <span class="quote-mark quote-mark--close" aria-hidden="true">&rdquo;</span>

    <svg class="wave-band" viewBox="0 0 1200 300" preserveAspectRatio="none" aria-hidden="true">
      <defs>
        <linearGradient id="wineWave" x1="0" y1="0" x2="1" y2="1">
          <stop offset="0" stop-color="#b51e45"/>
          <stop offset="0.5" stop-color="var(--wine)"/>
          <stop offset="1" stop-color="var(--wine-deep)"/>
        </linearGradient>
        <linearGradient id="roseWave" x1="0" y1="0" x2="1" y2="0">
          <stop offset="0" stop-color="var(--rose)"/>
          <stop offset="1" stop-color="var(--rose-pale)"/>
        </linearGradient>
      </defs>
      <path d="M0 30 C 300 -10, 650 40, 1200 150 L1200 300 L0 300 Z" fill="url(#roseWave)"/>
      <path d="M0 55 C 320 20, 700 90, 1200 210 L1200 300 L0 300 Z" fill="url(#wineWave)"/>
      <path d="M0 80 C 360 50, 760 120, 1200 240" fill="none" stroke="var(--rose-pale)" stroke-width="3" opacity="0.7"/>
      <path d="M0 105 C 380 80, 780 150, 1200 265" fill="none" stroke="var(--rose)" stroke-width="2" opacity="0.5"/>
      <rect x="0" y="275" width="1200" height="25" fill="var(--wine-deep)"/>
    </svg>

    <div class="brand">
      <div class="brand-name">Tornquill</div>
      <div class="brand-line">
        <span class="brand-services">MENTORING SERVICES</span>
        <span class="brand-url">tornquillmentoring.com</span>
      </div>
    </div>
    <div class="brand-badge" aria-hidden="true"></div>
  </main>
</body>
</html>
```